Pellham Grove Trust - New Website Designed

I need a site that looks like this http://www.quorlandgiving.org for boat donations. So please replace the cars with boats.

```html
<!DOCTYPE html>
<html lang="en">
<head>
<meta charset="utf-8">
<title>Pellham Grove Trust – Boat Donations</title>
<link rel="stylesheet" href="https://fonts.googleapis.com/css2?family=Mulish:wght@400;600;700;800&display=swap">
<style>
:root{
  --blue:#1f43b8;
  --blue-dark:#16309a;
  --blue-deep:#132a86;
  --red:#d9211d;
  --red-dark:#b0140f;
  --ink:#2b2b2b;
  --grey:#8a8a8a;
  --line:#d5d8de;
  --white:#ffffff;
}
*{box-sizing:border-box;margin:0;padding:0}
html,body{width:1200px;height:2479px;overflow:hidden;background:var(--white)}
body{font-family:"Mulish",Arial,sans-serif;color:var(--ink)}
.page{position:relative;width:1200px;height:2479px;overflow:hidden}
.abs{position:absolute}

/* header */
.brand{left:109px;top:48px;font-size:34px;font-weight:800;color:var(--blue);letter-spacing:-.3px}
.nav{left:0;top:129px;width:1200px;height:53px;background:linear-gradient(var(--blue),var(--blue-deep))}
.nav a{position:absolute;top:0;height:53px;line-height:53px;color:var(--white);font-size:18px;font-weight:700;text-decoration:none}
.nav .active{background:#0f2478;padding:0 32px}

/* hero */
.hero{left:0;top:182px;width:1200px;height:516px;background:linear-gradient(100deg,#6f7563 0%,#8d917f 30%,#c9ccc6 55%,#e7e9ea 75%,#b6b9a6 100%)}
.dots{left:558px;top:656px;display:flex;gap:8px}
.dots span{width:15px;height:15px;border-radius:50%;background:#bfc1c6;border:2px solid #fff}
.dots span:first-child{background:transparent;border-color:#9a9da3}

/* donate panel */
.panel-shape{left:739px;top:0}
.hotline{left:807px;top:51px;display:flex;align-items:center;gap:14px;color:var(--white)}
.phone-dot{width:46px;height:46px;border-radius:50%;background:var(--white);display:flex;align-items:center;justify-content:center}
.hotline small{display:block;font-size:19px;font-weight:600}
.hotline strong{display:block;font-size:27px;font-weight:700}
.ribbon-title{left:724px;top:124px;width:380px;height:58px;line-height:58px;text-align:center;color:var(--white);font-size:26px;font-weight:600}
.field{position:absolute;height:37px;background:var(--white);border:1px solid #e7b3b1;font-size:14px;color:#8a8a8a;padding:0 14px;line-height:35px}
.btn-donate{left:765px;top:504px;width:293px;height:46px;background:linear-gradient(#3a63d8,var(--blue-dark));color:var(--white);font-size:19px;font-weight:600;text-align:center;line-height:46px;border-radius:3px}

/* section titles */
.section-title{left:0;width:1200px;text-align:center;font-size:30px;font-weight:600;color:var(--ink)}
.divider{left:298px;width:611px;height:14px}

/* steps */
.step{position:absolute;width:330px;text-align:center}
.step-icon{position:absolute;width:108px;height:108px;border-radius:50%;border:3px solid var(--blue);background:var(--white);display:flex;align-items:center;justify-content:center}
.step-icon .core{width:88px;height:88px;border-radius:50%;background:var(--red);display:flex;align-items:center;justify-content:center}
.step-num{position:absolute;width:32px;height:32px;border-radius:50%;background:var(--blue);color:var(--white);font-size:19px;text-align:center;line-height:32px}
.step h3{font-size:22px;font-weight:600;color:var(--ink)}
.step p{margin-top:8px;font-size:14px;line-height:22px;color:var(--grey)}
.dash{position:absolute;top:884px;height:0;border-top:2px dashed #a9adb5}

/* why */
.why{left:0;top:1117px;width:1200px;height:483px;background:linear-gradient(90deg,#4c4640 0%,#6c6158 35%,#7a7066 60%,#55504c 100%)}
.why-shade{left:0;top:1117px;width:1200px;height:483px;background:rgba(30,30,35,.45)}
.notch{left:572px;top:1115px}
.why h2{left:0;top:1180px;width:1200px;text-align:center;color:var(--white);font-size:30px;font-weight:600}
.why-lead{left:200px;top:1238px;width:800px;text-align:center;color:var(--white);font-size:17px;line-height:30px}
.ticks{list-style:none;color:var(--white);font-size:15.5px}
.ticks li{height:36px;display:flex;align-items:center;gap:12px}
.tick{width:22px;height:22px;border-radius:50%;background:var(--white);display:flex;align-items:center;justify-content:center;flex:none}
.btn-outline{left:506px;top:1484px;width:188px;height:45px;border:2px solid var(--white);color:var(--white);font-size:18px;text-align:center;line-height:41px}

/* faq */
.faq{left:132px;width:465px}
.faq-item{height:46px;margin-bottom:12px;border:1px solid #cfd2d6;background:linear-gradient(#fbfbfb,#eceef0);font-size:15px;color:#444;padding:0 48px 0 18px;line-height:44px;position:relative;white-space:nowrap;overflow:hidden}
.faq-item .plus{position:absolute;right:10px;top:12px;width:20px;height:20px;border-radius:50%;background:var(--red)}
.faq-item .plus::before,.faq-item .plus::after{content:"";position:absolute;background:#fff;left:5px;top:9px;width:10px;height:2px}
.faq-item .plus::after{left:9px;top:5px;width:2px;height:10px}
.faq-photo{left:641px;top:1741px;width:430px;height:274px;background:linear-gradient(120deg,#6f7b4e,#a4a67e 45%,#cdbfa4 70%,#7d8457)}

/* footer */
.footer{left:0;top:2093px;width:1200px;height:319px;background:linear-gradient(135deg,#1d3fae,#2553c6 50%,#1b3aa6)}
.footer h4{position:absolute;top:2157px;color:var(--white);font-size:21px;font-weight:700}
.footer-about{left:129px;top:2210px;width:310px;color:var(--white);font-size:14px;line-height:21px}
.quick{left:523px;top:2201px;list-style:none}
.quick li{height:33px;color:var(--white);font-size:14px}
.social{position:absolute;top:2201px;width:38px;height:38px;border-radius:50%;border:2px solid var(--white)}
.footer-call{left:777px;top:2271px;width:289px;height:81px;border:2px solid var(--white);display:flex;align-items:center;gap:12px;padding-left:20px;color:var(--white)}
.footer-call .badge{width:46px;height:46px;border-radius:50%;background:var(--red);display:flex;align-items:center;justify-content:center}
.footer-call small{display:block;font-size:17px;font-weight:600}
.footer-call strong{display:block;font-size:24px;font-weight:700}
.copyright{left:0;top:2412px;width:1200px;height:67px;background:var(--blue-deep);color:#c8d1f0;font-size:13px;text-align:center;line-height:67px}
</style>
</head>
<body>
<div class="page">

  <!-- header -->
  <div class="abs brand">Pellham Grove Trust</div>
  <nav class="abs nav">
    <a class="active" style="left:117px">HOME</a>
    <a style="left:255px">ABOUT US</a>
    <a style="left:398px">WHY US</a>
    <a style="left:522px">HOW TO DONATE</a>
  </nav>

  <!-- hero -->
  <div class="abs hero" role="img" aria-label="Veteran in camouflage holding his child beside a white boat"></div>
  <div class="abs dots"><span></span><span></span><span></span><span></span></div>

  <!-- donation panel -->
  <svg class="abs panel-shape" width="380" height="620" viewBox="0 0 380 620" aria-hidden="true">
    <defs>
      <linearGradient id="panelRed" x1="0" y1="0" x2="0" y2="1">
        <stop offset="0" stop-color="#cf1f1b"/><stop offset="1" stop-color="#bf1713"/>
      </linearGradient>
    </defs>
    <path d="M0 0 H350 V612 Q300 590 210 585 Q120 580 60 600 Q20 610 0 590 Z" fill="url(#panelRed)"/>
    <path d="M0 540 Q80 600 200 585 Q290 575 350 612 L350 620 Q280 590 190 598 Q80 608 0 565 Z" fill="#1c3aa6" opacity=".9"/>
  </svg>
  <svg class="abs" style="left:724px;top:118px" width="380" height="72" viewBox="0 0 380 72" aria-hidden="true">
    <polygon points="0,6 15,0 15,6" fill="#8e0f0c"/>
    <polygon points="380,6 365,0 365,6" fill="#8e0f0c"/>
    <rect x="0" y="6" width="380" height="58" fill="#e02a25"/>
    <polygon points="15,64 15,72 0,64" fill="#8e0f0c"/>
    <polygon points="365,64 365,72 380,64" fill="#8e0f0c"/>
  </svg>
  <div class="abs hotline">
    <span class="phone-dot">
      <svg width="24" height="24" viewBox="0 0 24 24"><path d="M6.6 10.8a15 15 0 0 0 6.6 6.6l2.2-2.2c.3-.3.7-.4 1-.2 1.1.4 2.3.6 3.6.6.6 0 1 .4 1 1V20c0 .6-.4 1-1 1A17 17 0 0 1 3 4c0-.6.4-1 1-1h3.5c.6 0 1 .4 1 1 0 1.3.2 2.5.6 3.6.1.3 0 .7-.2 1z" fill="var(--red)"/></svg>
    </span>
    <span><small>Donate Boat Now!</small><strong>1-800-555-0142</strong></span>
  </div>
  <div class="abs ribbon-title">Donation Boat Online</div>
  <div class="field" style="left:765px;top:203px;width:146px">First Name</div>
  <div class="field" style="left:917px;top:203px;width:145px">Last Name</div>
  <div class="field" style="left:765px;top:248px;width:298px">Zip Code</div>
  <div class="field" style="left:765px;top:296px;width:298px">Phone</div>
  <div class="field" style="left:765px;top:344px;width:298px">Email address</div>
  <div class="field" style="left:765px;top:397px;width:146px">Choose Year</div>
  <div class="field" style="left:917px;top:397px;width:145px">Choose Make</div>
  <div class="field" style="left:765px;top:445px;width:298px">Model of Year</div>
  <div class="abs btn-donate">DONATE NOW</div>

  <!-- how to donate -->
  <h2 class="abs section-title" style="top:742px">HOW TO DONATE</h2>
  <svg class="abs divider" style="top:777px" viewBox="0 0 611 14" aria-hidden="true">
    <line x1="0" y1="7" x2="611" y2="7" stroke="var(--line)" stroke-width="1.5"/>
    <rect x="299" y="1" width="10" height="10" transform="rotate(45 304 6)" fill="var(--blue)"/>
  </svg>

  <div class="dash" style="left:325px;width:216px"></div>
  <div class="dash" style="left:659px;width:211px"></div>

  <div class="step-icon" style="left:212px;top:830px"><div class="core">
    <svg width="44" height="50" viewBox="0 0 44 50"><path d="M6 2h22l10 10v36H6z" fill="#fff"/><path d="M28 2v10h10" fill="none" stroke="var(--red)" stroke-width="2"/><g stroke="var(--red)" stroke-width="2.5"><line x1="12" y1="20" x2="32" y2="20"/><line x1="12" y1="27" x2="32" y2="27"/><line x1="12" y1="34" x2="26" y2="34"/></g></svg>
  </div></div>
  <div class="step-num" style="left:190px;top:868px">1</div>
  <div class="step" style="left:101px;top:952px"><h3>Call Us or Fill Our Form</h3><p>Aortor at ipsum cligula augue<br>bibendum accumsan vestibulum ut<br>commodos dictum metus</p></div>

  <div class="step-icon" style="left:546px;top:830px"><div class="core">
    <svg width="56" height="44" viewBox="0 0 56 44"><path d="M4 22h26v12H4z M30 16h12l8 10v8H30z" fill="none" stroke="#fff" stroke-width="3"/><line x1="12" y1="22" x2="26" y2="4" stroke="#fff" stroke-width="3"/><circle cx="13" cy="36" r="5" fill="#fff"/><circle cx="42" cy="36" r="5" fill="#fff"/></svg>
  </div></div>
  <div class="step-num" style="left:522px;top:868px">2</div>
  <div class="step" style="left:435px;top:952px"><h3>We Tow your Boat</h3><p>Aortor at ipsum cligula augue<br>bibendum accumsan vestibulum ut<br>commodos dictum metus</p></div>

  <div class="step-icon" style="left:875px;top:830px"><div class="core">
    <svg width="56" height="56" viewBox="0 0 56 56"><circle cx="28" cy="28" r="24" fill="none" stroke="#fff" stroke-width="3.5"/><line x1="11" y1="11" x2="45" y2="45" stroke="#fff" stroke-width="3.5"/><text x="28" y="34" text-anchor="middle" font-family="Mulish,Arial,sans-serif" font-size="16" font-weight="800" fill="#fff">TAX</text></svg>
  </div></div>
  <div class="step-num" style="left:854px;top:868px">3</div>
  <div class="step" style="left:764px;top:952px"><h3>Tax write Off</h3><p>Aortor at ipsum cligula augue<br>bibendum accumsan vestibulum ut<br>commodos dictum metus</p></div>

  <!-- why choose us -->
  <div class="abs why" role="img" aria-label="Smiling soldier with his family in front of a house with a flag"></div>
  <div class="abs why-shade"></div>
  <svg class="abs notch" width="56" height="22" viewBox="0 0 56 22" aria-hidden="true"><path d="M0 2 H56 Q40 4 28 20 Q16 4 0 2Z" fill="#fff"/><polyline points="20,7 28,13 36,7" fill="none" stroke="#333" stroke-width="2"/></svg>
  <h2 class="abs" style="left:0;top:1180px;width:1200px;text-align:center;color:#fff;font-size:30px;font-weight:600">WHY CHOOSE US</h2>
  <svg class="abs" style="left:420px;top:1218px" width="360" height="14" viewBox="0 0 360 14" aria-hidden="true">
    <line x1="0" y1="7" x2="360" y2="7" stroke="#fff" stroke-width="1.2" opacity=".8"/>
    <rect x="175" y="2" width="9" height="9" transform="rotate(45 180 7)" fill="#fff"/>
  </svg>
  <p class="abs why-lead">ullamcorper est eget tempor cursus neque mi consectetuer mi a ultricies massa est sed nisl Class aptent taciti sociosqu ad litora torquent per conubia nostra per inceptos</p>
  <ul class="abs ticks" style="left:159px;top:1325px">
    <li><span class="tick"><svg width="12" height="10" viewBox="0 0 12 10"><polyline points="1,5 4.5,8.5 11,1.5" fill="none" stroke="#555" stroke-width="2"/></svg></span>Vivamus porttitor purus nisi eleifend</li>
    <li><span class="tick"><svg width="12" height="10" viewBox="0 0 12 10"><polyline points="1,5 4.5,8.5 11,1.5" fill="none" stroke="#555" stroke-width="2"/></svg></span>libero a tempus libero lectus feugiat felis Morbi diam</li>
    <li><span class="tick"><svg width="12" height="10" viewBox="0 0 12 10"><polyline points="1,5 4.5,8.5 11,1.5" fill="none" stroke="#555" stroke-width="2"/></svg></span>Aauris viverra in gravida eu mattis in ante</li>
  </ul>
  <ul class="abs ticks" style="left:646px;top:1325px">
    <li><span class="tick"><svg width="12" height="10" viewBox="0 0 12 10"><polyline points="1,5 4.5,8.5 11,1.5" fill="none" stroke="#555" stroke-width="2"/></svg></span>Morbi eget arcu Morbi porta libero id ullamcorper</li>
    <li><span class="tick"><svg width="12" height="10" viewBox="0 0 12 10"><polyline points="1,5 4.5,8.5 11,1.5" fill="none" stroke="#555" stroke-width="2"/></svg></span>Nonummy nibh ligula pulvinar metus eget</li>
    <li><span class="tick"><svg width="12" height="10" viewBox="0 0 12 10"><polyline points="1,5 4.5,8.5 11,1.5" fill="none" stroke="#555" stroke-width="2"/></svg></span>Consectetuer augue nisi quis lacus Ut ac mi quis</li>
  </ul>
  <div class="abs btn-outline">Learn More</div>

  <!-- faq -->
  <h2 class="abs section-title" style="top:1663px;font-size:25px">FREQUENTLY ASKED QUESTIONS</h2>
  <div class="abs faq" style="top:1742px">
    <div class="faq-item">Praesent elementum elit at tellus nec ultricies sit amet<span class="plus"></span></div>
    <div class="faq-item">Porttitor mattis enim In massa libero interdum nec interdu<span class="plus"></span></div>
    <div class="faq-item">Sed nulla In ullamcorper est eget tempor cursus<span class="plus"></span></div>
    <div class="faq-item">Pellentesque habitant morbi tristiq<span class="plus"></span></div>
    <div class="faq-item">Neque mi consectetuer mi a ultricies massa est<span class="plus"></span></div>
  </div>
  <div class="abs faq-photo" role="img" aria-label="Soldier outdoors carrying his daughter on his back"></div>

  <!-- footer -->
  <footer class="abs footer" role="img" aria-label="Waving flags in soft blue tones"></footer>
  <h4 style="position:absolute;left:129px;top:2157px;color:#fff;font-size:21px;font-weight:700">ABOUT PELLHAM GROVE TRUST</h4>
  <h4 style="position:absolute;left:521px;top:2157px;color:#fff;font-size:21px;font-weight:700">QUICK LINKS</h4>
  <h4 style="position:absolute;left:779px;top:2157px;color:#fff;font-size:21px;font-weight:700">FOLLOW US</h4>
  <p class="abs footer-about">Praesent elementum elit at tellus nec ultricies sit amet porttitor mattis enim In massa libero interdum nec interdum vel blandit sed nulla In ullamcorper est eget tempor cursus neque mi consectetuer mi a ultricies massa est sed nisl Class ap</p>
  <ul class="abs quick">
    <li>About Us</li><li>Why Choose Us</li><li>How to Donate</li><li>Contact Us</li>
  </ul>
  <span class="social" style="left:779px"></span>
  <span class="social" style="left:824px"></span>
  <span class="social" style="left:870px"></span>
  <span class="social" style="left:917px"></span>
  <div class="abs footer-call">
    <span class="badge"><svg width="24" height="24" viewBox="0 0 24 24"><path d="M6.6 10.8a15 15 0 0 0 6.6 6.6l2.2-2.2c.3-.3.7-.4 1-.2 1.1.4 2.3.6 3.6.6.6 0 1 .4 1 1V20c0 .6-.4 1-1 1A17 17 0 0 1 3 4c0-.6.4-1 1-1h3.5c.6 0 1 .4 1 1 0 1.3.2 2.5.6 3.6.1.3 0 .7-.2 1z" fill="#fff"/></svg></span>
    <span><small>Donate Boat Now!</small><strong>1-800-555-0142</strong></span>
  </div>
  <div class="abs copyright">© 2017 Company Name &nbsp;All right reserved &nbsp;Term of Use</div>

</div>
</body>
</html>
```